Roofing web site brvt roofing

Look at some of our competitors web page we like something similar with NYC roofing
https://www.quillbarroofing.example/
Maybe a skyline picture of nyc at the home page with a picture of flat roofing installation

Target Market(s)

Commercial and residential flat roofs

Industry/Entity Type

Flat Roofing industry

Coding

Coded - Design and coding required

Number of Pages Required

2 page

Font styles to use
Decorative
Script

Colors

Designer to choose colors to be used in the design.

Requirements
Must have
• At BRVT Roofing, we are a trusted and reputable roofing company specializing in new construction flat roof installation and repair. With years of experience in the industry, we take pride in providing exceptional roofing solutions to our valued clients. Our team of highly skilled and dedicated roofing professionals understands the unique challenges and requirements of new construction projects. We work closely with builders, contractors, and architects to design and install flat roofs that meet the specific needs of each project. From commercial buildings to residential complexes, we have the expertise to deliver reliable and durable roofing solutions. When it comes to flat roof repairs, we are your go-to experts. Our experienced technicians conduct thorough inspections to identify the root cause of any issues your roof may be experiencing. We utilize the latest industry techniques and high-quality materials to efficiently repair your flat roof, ensuring its integrity and longevity. At BRVT Roofing, we prioritize customer satisfaction above all else. We believe in building strong relationships with our clients by providing exceptional craftsmanship and outstanding customer service. Our team is dedicated to delivering projects on time, within budget, and to the highest standards of quality. We understand that a well-maintained roof is essential for protecting your property and ensuring the safety of its occupants. That's why we use only the best materials and employ skilled professionals who are trained in the latest roofing practices. Our commitment to excellence is evident in every project we undertake. As a fully licensed and insured roofing company, we prioritize safety and adhere to industry regulations and best practices. We take every precaution to create a safe working environment for our team and minimize any disruptions to your daily routine. When you choose BRVT Roofing, you can trust that you are working with a reliable and reputable company that will deliver exceptional results. We are committed to exceeding your expectations and providing you with a roof that is built to last. Contact us today for all your new construction flat roof installation and repair needs.
Nice to have
• NYC skyline background with commercial roofing pictures of torching roofing

```html
<!DOCTYPE html>
<html lang="en">
<head>
<meta charset="utf-8">
<title>BRVT Roofing</title>
<link href="https://fonts.googleapis.com/css2?family=Gelasio:wght@400;500;600&family=Montserrat:wght@500;600;700;800&display=swap" rel="stylesheet">
<style>
:root{
  --orange:#f26522;
  --ink:#1c1c1c;
  --text:#3a3a3a;
  --dark:#16181c;
  --darker:#0b0b0c;
  --white:#ffffff;
  --muted:#cfcfcf;
  --serif:'Gelasio',Georgia,serif;
  --sans:'Montserrat',Arial,sans-serif;
}
*{box-sizing:border-box;margin:0;padding:0}
html,body{width:1200px;height:4022px;overflow:hidden}
body{position:relative;background:var(--white);font-family:var(--serif);color:var(--text)}
.photo{position:absolute}

/* header */
.site-header{position:absolute;left:0;top:0;width:1200px;height:117px;border-top:4px solid var(--orange);background:#fff}
.logo-box{position:absolute;left:112px;top:28px;width:110px;height:60px;border:2px solid #555;display:flex;align-items:center;justify-content:center;text-align:center;font-family:var(--serif);font-size:19px;line-height:20px;color:#333}
.top-contact{position:absolute;top:22px;font-family:var(--sans);font-size:13px;color:#333;display:flex;align-items:center;gap:10px}
.main-nav{position:absolute;top:72px;right:116px;display:flex;gap:40px;font-family:var(--serif);font-size:13px;letter-spacing:1px;color:#222}
.main-nav .active{color:var(--orange)}
.header-icons{position:absolute;top:24px;right:116px;display:flex;gap:14px}

/* hero */
.hero{position:absolute;left:0;top:117px;width:1200px;height:573px;background:linear-gradient(180deg,#2d4866 0%,#557593 45%,#7e8c98 75%,#6d6b68 100%)}
.hero-welcome{position:absolute;left:112px;top:165px;font-family:var(--sans);font-weight:600;font-size:27px;letter-spacing:3px;color:#fff}
.hero-title{position:absolute;left:112px;top:207px;font-family:var(--sans);font-weight:800;font-size:40px;line-height:46px;letter-spacing:3px;color:#fff}
.hero-list{position:absolute;left:112px;top:317px;list-style:none;font-family:var(--sans);font-weight:600;font-size:20px;letter-spacing:1.5px;color:#fff}
.hero-list li{display:flex;align-items:center;gap:14px;height:31px}
.btn{display:inline-block;background:var(--orange);color:#fff;font-family:var(--sans);font-weight:600;font-size:13px;letter-spacing:1px;outline:2px solid var(--orange);border:2px solid #fff;text-align:center}
.hero .btn{position:absolute;left:112px;top:436px;width:124px;height:37px;line-height:33px}

/* about */
.about-title{position:absolute;left:636px;top:770px;font-family:var(--serif);font-size:38px;letter-spacing:3px;color:var(--ink)}
.about-title span,.why-title span{color:var(--orange)}
.about-text{position:absolute;left:636px;top:845px;width:455px;font-size:14px;line-height:21.5px;letter-spacing:1px;text-align:justify;color:#333}
.about-text p{margin-bottom:18px}
.about .btn{position:absolute;left:638px;top:1207px;width:124px;height:37px;line-height:33px}

/* services */
.services{position:absolute;left:0;top:1358px;width:1200px;height:729px;background:linear-gradient(180deg,#1d1f23,#2b2d30 60%,#222428)}
.section-title-light{position:absolute;left:0;width:1200px;text-align:center;font-family:var(--serif);font-size:37px;letter-spacing:4px;color:#fff}
.kicker{position:absolute;left:0;width:1200px;text-align:center;font-size:13px;letter-spacing:1.5px;color:var(--orange)}
.service-card{position:absolute;top:185px;width:309px;height:475px;background:#fff;border-radius:10px;overflow:hidden}
.service-card .photo{left:0;top:0;width:309px;height:227px}
.card-icon{position:absolute;left:12px;top:200px;width:50px;height:50px;border-radius:50%;background:#fff;display:flex;align-items:center;justify-content:center}
.card-title{position:absolute;left:0;top:243px;width:100%;text-align:center;padding-left:30px;font-size:19px;font-weight:400;letter-spacing:1.5px;color:var(--ink)}
.card-text{position:absolute;left:17px;top:295px;width:275px;font-size:13px;line-height:19.5px;letter-spacing:.8px;color:#333}
.card-link{position:absolute;left:21px;top:435px;font-size:13px;letter-spacing:1px;color:var(--orange);border-bottom:1px solid var(--orange);padding-bottom:2px}

/* why */
.why-title{position:absolute;left:110px;top:2170px;font-family:var(--serif);font-weight:400;font-size:38px;letter-spacing:4px;color:var(--ink)}
.why-list{position:absolute;left:604px;top:2305px;list-style:none}
.why-list li{display:flex;align-items:center;height:76.3px;font-size:18px;letter-spacing:2px;color:#222}
.tick-circle{width:58px;height:58px;border-radius:50%;background:#fff;box-shadow:0 2px 10px rgba(0,0,0,.15);display:flex;align-items:center;justify-content:center;margin-right:24px}

/* features */
.features{position:absolute;left:0;top:2863px;width:1200px;height:377px;background:linear-gradient(90deg,#1b1d22,#2a2c30 50%,#1d1f24)}
.feature{position:absolute;top:85px;width:280px;text-align:center;color:#fff}
.feature h3{font-weight:400;font-size:22px;letter-spacing:2px;margin:14px 0 10px}
.feature p{font-size:14.5px;line-height:22px;letter-spacing:1.5px;color:#e8e8e8;padding:0 42px}
.feature-divider{position:absolute;top:90px;height:235px;border-left:2px dashed #c9c9c9}

/* newsletter */
.news-title{position:absolute;left:0;width:1200px;text-align:center;font-weight:400;font-size:37px;letter-spacing:4px;color:var(--ink)}
.news-title.accent{color:var(--orange)}
.news-sub{position:absolute;left:0;top:3424px;width:1200px;text-align:center;font-size:16px;letter-spacing:1.5px;color:#444}
.news-form{position:absolute;left:313px;top:3480px;width:574px;height:55px;background:#fff;box-shadow:0 2px 12px rgba(0,0,0,.12);display:flex}
.news-form .field{flex:1;padding-left:28px;line-height:55px;font-size:14px;letter-spacing:1px;color:#555}
.news-form .btn{width:135px;height:51px;margin:2px;line-height:47px;font-family:var(--serif);font-size:16px;color:#222}

/* footer */
.site-footer{position:absolute;left:0;top:3622px;width:1200px;height:400px;background:var(--darker);color:#fff}
.footer-logo{position:absolute;left:114px;top:83px;width:150px;height:80px;border:2px solid #fff;display:flex;align-items:center;justify-content:center;text-align:center;font-size:29px;line-height:30px}
.socials{position:absolute;left:118px;top:203px;display:flex;gap:5px}
.socials span{width:28px;height:28px;border-radius:3px;display:flex;align-items:center;justify-content:center}
.socials i{width:10px;height:10px;border-radius:50%;background:#fff}
.footer-col{position:absolute;top:105px}
.footer-col h4{font-weight:400;font-size:18px;letter-spacing:2px;margin-bottom:14px}
.footer-col a{display:block;font-size:14px;letter-spacing:1.5px;line-height:32.5px;color:#fff;text-decoration:none}
.contact-row{display:flex;gap:14px;align-items:flex-start;font-family:var(--sans);font-size:13px;line-height:20px;letter-spacing:.8px;margin-bottom:22px}
.contact-icon{width:28px;height:28px;border:1px solid #fff;border-radius:3px;display:flex;align-items:center;justify-content:center;flex:none}
.footer-rule{position:absolute;left:104px;top:348px;width:980px;border-top:1px solid #777}
.copyright{position:absolute;left:0;top:376px;width:1200px;text-align:center;font-family:var(--sans);font-size:10px;letter-spacing:1px}
</style>
</head>
<body>

<header class="site-header">
  <div class="logo-box">BRVT<br>Roofing</div>
  <div class="top-contact" style="left:622px">
    <svg width="16" height="12" viewBox="0 0 16 12"><rect width="16" height="12" rx="1" fill="#f26522"/><path d="M1 1l7 6 7-6" stroke="#fff" stroke-width="1.4" fill="none"/></svg>
    info@brvtroofing
  </div>
  <div class="top-contact" style="left:828px">
    <svg width="15" height="15" viewBox="0 0 24 24"><path fill="#f26522" d="M6.6 10.8a15 15 0 006.6 6.6l2.2-2.2a1 1 0 011-.25 11.4 11.4 0 003.6.6 1 1 0 011 1V20a1 1 0 01-1 1A17 17 0 013 4a1 1 0 011-1h3.5a1 1 0 011 1c0 1.25.2 2.45.6 3.6a1 1 0 01-.25 1z"/></svg>
    555-014-2290
  </div>
  <div class="header-icons">
    <svg width="15" height="15" viewBox="0 0 16 16"><circle cx="6.5" cy="6.5" r="5" stroke="#444" stroke-width="1.5" fill="none"/><path d="M10.5 10.5L15 15" stroke="#444" stroke-width="1.5"/></svg>
    <svg width="14" height="16" viewBox="0 0 14 16"><rect x="1" y="5" width="12" height="10" stroke="#444" stroke-width="1.5" fill="none"/><path d="M4 5V3.5a3 3 0 016 0V5" stroke="#444" stroke-width="1.5" fill="none"/></svg>
    <svg width="14" height="16" viewBox="0 0 14 16"><circle cx="7" cy="5" r="3.5" stroke="#444" stroke-width="1.5" fill="none"/><path d="M1 15a6 6 0 0112 0z" stroke="#444" stroke-width="1.5" fill="none"/></svg>
  </div>
  <nav class="main-nav">
    <span class="active">HOME</span><span>CONTACT US</span><span>PHOTO GALLERY</span><span>SERVICES</span><span>ABOUT US</span>
  </nav>
</header>

<section class="hero" role="img" aria-label="City skyline by the water with a roofer in a hard hat rolling out flat roofing membrane">
  <div class="hero-welcome">Welcome To</div>
  <h1 class="hero-title">Professional &amp; Affordable<br>Roofing Services.</h1>
  <ul class="hero-list">
    <li><svg width="18" height="16" viewBox="0 0 18 16"><path d="M2 9l5 5L16 2" stroke="#fff" stroke-width="2.4" fill="none"/></svg>Storm damage</li>
    <li><svg width="18" height="16" viewBox="0 0 18 16"><path d="M2 9l5 5L16 2" stroke="#fff" stroke-width="2.4" fill="none"/></svg>Roof installation</li>
    <li><svg width="18" height="16" viewBox="0 0 18 16"><path d="M2 9l5 5L16 2" stroke="#fff" stroke-width="2.4" fill="none"/></svg>Roof repair</li>
  </ul>
  <span class="btn">Book Now</span>
</section>

<section class="about">
  <div class="photo" style="left:111px;top:778px;width:445px;height:244px;background:linear-gradient(180deg,#8fb4d8,#b9b4a8 55%,#4a4b4d)" role="img" aria-label="Roofer in a safety vest torching roll roofing next to a high-rise under construction"></div>
  <div class="photo" style="left:111px;top:1026px;width:445px;height:244px;background:linear-gradient(180deg,#5f7a44,#5d5f60 35%,#3f4144)" role="img" aria-label="Rolls of roofing membrane with a lit torch on a flat roof"></div>
  <h2 class="about-title">About <span>Us</span></h2>
  <div class="about-text">
    <p>At BRVT Roofing, we are a trusted and reputable roofing company specializing in new construction flat roof installation and repair. With years of experience in the industry, we take pride in providing exceptional roofing solutions to our valued clients.</p>
    <p>Our team of highly skilled and dedicated roofing professionals understands the unique challenges and requirements of new construction projects.</p>
    <p>We work closely with builders, contractors, and architects to design and install flat roofs that meet the specific needs of each project. From commercial buildings to residential complexes, we have the expertise to deliver reliable and durable roofing solutions.</p>
  </div>
  <span class="btn">Read More</span>
</section>

<section class="services">
  <h2 class="section-title-light" style="top:52px;font-weight:400">Expert Flat Roof Services</h2>
  <div class="kicker" style="top:116px">PROS IN ALL ASPECTS OF ROOFING</div>

  <article class="service-card" style="left:110px">
    <div class="photo" style="background:linear-gradient(180deg,#9ab6cf,#6b7c90 55%,#3d4150)" role="img" aria-label="Roofer in a hard hat and ear protection laying membrane"></div>
    <div class="card-icon"><svg width="30" height="30" viewBox="0 0 30 30"><circle cx="12" cy="6" r="3" fill="#222"/><path d="M6 24l5-12 5 4 5-2M4 26h22" stroke="#222" stroke-width="2.5" fill="none"/></svg></div>
    <h3 class="card-title">Perfect Installs</h3>
    <p class="card-text" style="text-align:justify">Your roof is your main defense against the elements. Let us walk you through the best options to fit your needs and once you feel comfortable with your choice, we'll handle the complete installation.</p>
    <span class="card-link">Findout More.....</span>
  </article>

  <article class="service-card" style="left:444px">
    <div class="photo" style="background:linear-gradient(180deg,#a9c0d6,#7d8a98 60%,#3c3f45)" role="img" aria-label="Worker in winter gear operating roofing equipment against a city view"></div>
    <div class="card-icon"><svg width="26" height="30" viewBox="0 0 26 30"><circle cx="13" cy="19" r="8" stroke="#222" stroke-width="3" fill="none"/><circle cx="13" cy="19" r="3" fill="#222"/><rect x="9" y="2" width="8" height="7" fill="#222"/></svg></div>
    <h3 class="card-title">Reliable Upgrades</h3>
    <p class="card-text">If you're looking to update or upgrade your roofing and gutters, we've got you covered. Book a free consultation to discuss our different types of roofing composition and environmentally friendly options!</p>
    <span class="card-link" style="left:17px">Findout More.....</span>
  </article>

  <article class="service-card" style="left:778px">
    <div class="photo" style="background:linear-gradient(180deg,#b9c2c8,#6d7276 50%,#2a2b2e)" role="img" aria-label="Close-up of a torch flame heating a roll of membrane"></div>
    <div class="card-icon"><svg width="30" height="30" viewBox="0 0 30 30"><circle cx="15" cy="15" r="10" stroke="#222" stroke-width="3" fill="none"/><path d="M8 22L22 8" stroke="#222" stroke-width="3"/></svg></div>
    <h3 class="card-title">Upkeep &amp; Repair</h3>
    <p class="card-text" style="text-align:justify">Age and environmental factors can wreak havoc on your roof. Ignoring problems for too long can cause headaches down the road. Start with a free inspection today!</p>
    <span class="card-link">Findout More.....</span>
  </article>
</section>

<section class="why">
  <h2 class="why-title">Why Choose <span>BRVT</span> <span>Construction</span></h2>
  <div class="photo" style="left:111px;top:2276px;width:527px;height:497px;background:linear-gradient(180deg,#c9d6e0,#a9b0a4 35%,#6b6f72 60%,#4f5256)" role="img" aria-label="Roofer in blue overalls and hard hat torching the edge of a flat roof"></div>
  <ul class="why-list">
    <li><span class="tick-circle"><svg width="22" height="18" viewBox="0 0 22 18"><path d="M2 9l6 6L20 2" stroke="#f26522" stroke-width="3.5" fill="none"/></svg></span>Licensed,Bonded,&amp; Insured</li>
    <li><span class="tick-circle"><svg width="22" height="18" viewBox="0 0 22 18"><path d="M2 9l6 6L20 2" stroke="#f26522" stroke-width="3.5" fill="none"/></svg></span>Reliable &amp; Experienced Professionals</li>
    <li><span class="tick-circle"><svg width="22" height="18" viewBox="0 0 22 18"><path d="M2 9l6 6L20 2" stroke="#f26522" stroke-width="3.5" fill="none"/></svg></span>Free Evaluations &amp; Estimates</li>
    <li><span class="tick-circle"><svg width="22" height="18" viewBox="0 0 22 18"><path d="M2 9l6 6L20 2" stroke="#f26522" stroke-width="3.5" fill="none"/></svg></span>Lead - Safe Certified</li>
    <li><span class="tick-circle"><svg width="22" height="18" viewBox="0 0 22 18"><path d="M2 9l6 6L20 2" stroke="#f26522" stroke-width="3.5" fill="none"/></svg></span>24/7 Emergency Response</li>
    <li><span class="tick-circle"><svg width="22" height="18" viewBox="0 0 22 18"><path d="M2 9l6 6L20 2" stroke="#f26522" stroke-width="3.5" fill="none"/></svg></span>QRA Accredited Business</li>
  </ul>
</section>

<section class="features" role="img" aria-label="Dim background of roofers working on a rooftop">
  <div class="feature" style="left:128px">
    <svg width="50" height="50" viewBox="0 0 50 50"><path d="M20 4l14 6v12c0 10-6 17-14 20C12 39 6 32 6 22V10z" stroke="#fff" stroke-width="3" fill="none"/><path d="M20 14c-4 6-5 8-5 10a5 5 0 0010 0c0-2-1-4-5-10z" fill="#fff"/><circle cx="38" cy="38" r="9" fill="#fff"/><path d="M33 38l4 4 6-7" stroke="#222" stroke-width="2.5" fill="none"/></svg>
    <h3>Roof Leak Repairs</h3>
    <p>Flat roofing maintenance includes drain- ing water, repairing your roof's infiltration system, and getting rid of debris.</p>
  </div>
  <div class="feature-divider" style="left:432px"></div>
  <div class="feature" style="left:458px">
    <svg width="50" height="50" viewBox="0 0 50 50"><path d="M26 4L14 26h10l-6 20 18-26H26l6-16z" fill="#fff"/></svg>
    <h3>Flashing Servics</h3>
    <p>Roof flashing plays an important role in leak prevention at the most vulnerable areas of your roof</p>
  </div>
  <div class="feature-divider" style="left:758px"></div>
  <div class="feature" style="left:813px">
    <svg width="50" height="50" viewBox="0 0 50 50"><g fill="#fff"><path d="M10 6c-4 6-5 8-5 10a5 5 0 0010 0c0-2-1-4-5-10z"/><path d="M25 6c-4 6-5 8-5 10a5 5 0 0010 0c0-2-1-4-5-10z"/><path d="M40 6c-4 6-5 8-5 10a5 5 0 0010 0c0-2-1-4-5-10z"/><rect x="4" y="26" width="42" height="4"/><rect x="4" y="36" width="42" height="4"/><rect x="8" y="26" width="4" height="18"/><rect x="23" y="26" width="4" height="18"/><rect x="38" y="26" width="4" height="18"/></g></svg>
    <h3>Waterproofing Experts</h3>
    <p>Our highly-skilled technicians will expertly diagnose your problem areas and provide you solution to your specific need.</p>
  </div>
</section>

<section class="newsletter">
  <h2 class="news-title" style="top:3320px">Flat roof installation roof repair storm</h2>
  <h2 class="news-title accent" style="top:3365px">damage insurance specialists</h2>
  <p class="news-sub">Sign up to receive maintenance reminders and hear about our latest projects.</p>
  <div class="news-form"><span class="field">Email</span><span class="btn">Sign Up</span></div>
</section>

<footer class="site-footer">
  <div class="footer-logo">BRVT<br>Roofing</div>
  <div class="socials">
    <span style="background:#1877f2"><i></i></span>
    <span style="background:#111;border:1px solid #555"><i></i></span>
    <span style="background:#e60023"><i></i></span>
    <span style="background:#d62976"><i></i></span>
    <span style="background:#e00"><i></i></span>
  </div>
  <div class="footer-col" style="left:435px">
    <h4>Quick Links</h4>
    <a>Home</a><a>Contact Us</a><a>Photo Gallery</a><a>About Us</a><a>Services</a>
  </div>
  <div class="footer-col" style="left:633px">
    <h4>Other Links</h4>
    <a>Privacy Policy</a><a>Terms Of Service</a>
  </div>
  <div class="footer-col" style="left:895px">
    <h4>Contact Us</h4>
    <div class="contact-row"><span class="contact-icon"><svg width="12" height="16" viewBox="0 0 12 16"><path d="M6 1a5 5 0 015 5c0 4-5 9-5 9S1 10 1 6a5 5 0 015-5z" stroke="#fff" stroke-width="1.5" fill="none"/><circle cx="6" cy="6" r="1.8" fill="#fff"/></svg></span><span>Lorem IPsum,<br>Usa - 437916</span></div>
    <div class="contact-row"><span class="contact-icon"><svg width="14" height="14" viewBox="0 0 24 24"><path fill="#fff" d="M6.6 10.8a15 15 0 006.6 6.6l2.2-2.2a1 1 0 011-.25 11.4 11.4 0 003.6.6 1 1 0 011 1V20a1 1 0 01-1 1A17 17 0 013 4a1 1 0 011-1h3.5a1 1 0 011 1c0 1.25.2 2.45.6 3.6a1 1 0 01-.25 1z"/></svg></span><span>555-014-2290</span></div>
    <div class="contact-row"><span class="contact-icon"><svg width="14" height="11" viewBox="0 0 16 12"><rect width="16" height="12" rx="1" fill="#fff"/><path d="M1 1l7 6 7-6" stroke="#0b0b0c" stroke-width="1.4" fill="none"/></svg></span><span>info@brvtroofing.example</span></div>
  </div>
  <div class="footer-rule"></div>
  <div class="copyright">COPYRIGHT © 2024 BRVT CONSTRUCTION ROOFING - ALL RIGHTS RESERVED.</div>
</footer>

</body>
</html>
```